Website for IT consulting Company

I need a website upgrade, the existing site content is ok, I would also like to add a testimonial page, the site should be something that is easy for us to update content. You use the content from www.kelvanbrook.com as an example. I will also post update logo and artwork. I also need a contact form with some type of validation or captcha.

I added Coded to the Project

Please omit Address maps

Target Market(s)

small business, service oriented companies. We provide IT Consulting, support and mangement

Industry/Entity Type

Information Technology

Coding

Number of Pages Required

1 page

Font styles to use
Serif
Sans Serif

Requirements
Must have
• Contain logo attached, and content from existing web site www.kelvanbrook.com.
• Also need to update content easily, and be movable to different platforms.
• There is a catch phrase
• "Let us worry about your technology…” “ so you don’t have to!”
• Should be included.
Nice to have
• Testimonial page, Project page where we can post new and past projects and pictures
Should not have
• none

```html
<!DOCTYPE html>
<html lang="en">
<head>
<meta charset="utf-8">
<title>Kelvanbrook Technology Group</title>
<link rel="stylesheet" href="https://fonts.googleapis.com/css2?family=Exo+2:ital,wght@0,700;1,700;1,800&family=Open+Sans:ital,wght@0,400;0,600;0,700;1,400&display=swap">
<style>
:root{
  --orange:#f39325;
  --orange-deep:#ee7622;
  --ink:#1d1d1d;
  --grey:#6b6b6b;
  --grey-light:#e9e9e9;
  --line:#d0d0d0;
  --white:#fff;
  --navy:#1f4e8c;
  --footer:#3a3634;
}
*{box-sizing:border-box;margin:0;padding:0}
html,body{width:1200px;height:2276px;overflow:hidden}
body{font-family:"Open Sans",Arial,sans-serif;color:var(--ink);background:var(--white);position:relative}
.display{font-family:"Exo 2","Arial Black",sans-serif;font-style:italic;font-weight:800}
.accent{color:var(--orange)}

.top-bar{height:36px;background:#000;display:flex;justify-content:flex-end;align-items:center;gap:8px;padding-right:84px}
.top-bar span{width:28px;height:28px;background:#8a8a8a;border:2px solid #bdbdbd}

.site-header{height:88px;display:flex;align-items:center;justify-content:space-between;padding:0 88px 0 80px}
.brand{display:flex;align-items:center;gap:12px}
.brand-mark{width:44px;height:44px;background:var(--orange)}
.brand-name{font-family:"Exo 2",sans-serif;font-weight:700;font-size:46px;color:#7a7a7a;letter-spacing:1px}
.header-phone{display:flex;align-items:center;gap:14px;font-family:"Exo 2",sans-serif;font-style:italic;font-weight:700;font-size:21px;color:#555}
.header-phone .ico{width:28px;height:28px;background:var(--orange);display:flex;align-items:center;justify-content:center}

.main-nav{height:57px;background:linear-gradient(90deg,var(--orange),var(--orange-deep));display:flex;align-items:center;justify-content:space-between;padding:0 70px 0 92px}
.main-nav a{color:var(--white);text-decoration:none;font-size:19px;letter-spacing:.5px;height:57px;line-height:57px}
.main-nav a.current{background:#000;padding:0 8px}

.hero{height:534px;position:relative;background:linear-gradient(120deg,#d9dde2 0%,#9ca8b6 30%,#c9c2b8 55%,#e8e4df 80%,#a9a39c 100%)}
.hero-tagline{position:absolute;left:0;right:0;bottom:0;height:55px;background:rgba(30,30,30,.78);text-align:center;line-height:55px;font-size:33px;color:var(--white)}

.about{height:426px;position:relative}
.about-copy{position:absolute;left:82px;top:60px;width:650px}
.about-copy .section-title{font-size:24px;letter-spacing:.3px;white-space:nowrap}
.about-copy .rule{width:80px;height:2px;background:var(--orange);margin:8px 0 18px}
.about-copy p{font-size:14px;line-height:26px}
.pillars{display:flex;gap:36px;margin-top:36px}
.pillar{display:flex;gap:18px;width:310px}
.pillar-icon{width:70px;height:68px;border:2px solid #c6c6c6;border-radius:6px;background:linear-gradient(#8a8a8a,#5b5b5b);flex:none;display:flex;align-items:center;justify-content:center}
.pillar h3{font-size:20px;font-weight:600;margin-bottom:2px}
.pillar p{font-size:14px;line-height:25px}

.inquiry{position:absolute;left:766px;top:50px;width:354px;height:324px;background:var(--grey-light);border:1px solid var(--line)}
.inquiry-tab{position:absolute;left:45px;top:-15px;width:264px;height:46px;background:linear-gradient(#a8a8a8,#6e6e6e);color:var(--white);font-size:21px;text-align:center;line-height:46px;border:2px solid #e2e2e2}
.inquiry form{padding:50px 20px 0}
.inquiry .field{height:34px;background:var(--white);border:1px solid #ccc;border-radius:3px;margin-bottom:8px;font-size:12.5px;color:#333;padding:0 10px;line-height:32px}
.inquiry .call{text-align:center;margin:20px 0 10px;font-size:21px}
.inquiry .call em{color:var(--orange);font-style:normal;font-family:"Open Sans",sans-serif;font-weight:400;font-size:17px;margin-right:8px}
.inquiry .submit{display:block;margin:0 auto;width:122px;height:35px;background:var(--orange);color:var(--white);text-align:center;line-height:35px;font-size:18px}

.services{height:406px;background:var(--grey-light);position:relative}
.services .section-title{text-align:center;padding-top:42px;font-size:32px}
.service-card{position:absolute;top:152px;width:314px;height:185px;background:var(--white);border-radius:14px;box-shadow:0 6px 8px rgba(0,0,0,.25);text-align:center}
.service-icon{width:72px;height:72px;margin:-34px auto 0;border:2px solid #ddd;display:flex;align-items:center;justify-content:center}
.service-card h4{font-family:"Exo 2",sans-serif;font-style:italic;font-weight:700;font-size:15px;color:#555;margin-top:32px}
.service-card p{font-size:13px;line-height:20px;color:#333;margin:14px 34px 0}
.service-card .more{position:absolute;left:143px;bottom:-2px;width:28px;height:24px;background:#777;color:var(--white);font-size:18px;line-height:24px}

.testimonials{height:357px;position:relative;text-align:center}
.testimonials .section-title{padding-top:50px;font-size:32px}
.testimonials .divider{width:290px;height:1px;background:#aaa;margin:10px auto 0;position:relative}
.testimonials .divider::after{content:"";position:absolute;left:125px;top:-1px;width:40px;height:3px;background:var(--navy)}
.quote{font-style:italic;font-size:15.5px;line-height:30px;width:800px;margin:42px auto 0;color:#222;position:relative}
.quote .mark{font-family:Georgia,serif;font-size:42px;color:#aaa;line-height:0;position:relative;top:14px}
.author{color:var(--navy);font-weight:700;font-size:18px;margin-top:20px}
.place{font-weight:700;font-size:15px;margin-top:4px}
.arrow{position:absolute;top:192px}

.site-footer{height:326px;position:relative;background:linear-gradient(180deg,#4a4440 0%,#35302d 55%,#2a2624 100%);color:var(--white)}
.footer-col{position:absolute;top:52px}
.footer-col h5{font-size:20px;font-weight:400;padding-bottom:14px;border-bottom:1px solid rgba(255,255,255,.15);margin-bottom:14px}
.quick-links li{list-style:none;font-size:14px;line-height:25px;padding-left:18px;position:relative}
.quick-links li::before{content:"";position:absolute;left:0;top:10px;width:5px;height:5px;border-radius:50%;background:var(--orange)}
.contact-lines p{font-size:14px;line-height:25px}
.contact-lines .row{display:flex;align-items:center;gap:12px;margin-top:12px;font-size:14px}
.social-list .row{display:flex;align-items:center;gap:16px;margin-bottom:14px;font-size:14px}
.social-list .sq{width:28px;height:28px;background:#9a9a9a}
.copyright{height:46px;background:linear-gradient(#9a9a9a,#6f6f6f);color:var(--white);text-align:center;line-height:46px;font-size:15px;font-weight:700}
</style>
</head>
<body>

<div class="top-bar" aria-label="Social links"><span></span><span></span><span></span><span></span></div>

<header class="site-header">
  <div class="brand"><span class="brand-mark"></span><span class="brand-name">KELVANBROOK</span></div>
  <div class="header-phone">
    <span class="ico"><svg width="16" height="16" viewBox="0 0 24 24"><path fill="#1d1d1d" d="M6.6 10.8a15 15 0 0 0 6.6 6.6l2.2-2.2c.3-.3.7-.4 1-.2 1.1.4 2.3.6 3.6.6.6 0 1 .4 1 1V20c0 .6-.4 1-1 1A17 17 0 0 1 3 4c0-.6.4-1 1-1h3.5c.6 0 1 .4 1 1 0 1.2.2 2.4.6 3.6.1.3 0 .7-.2 1z"/></svg></span>
    (555) 014-2287
  </div>
</header>

<nav class="main-nav display">
  <a class="current">HOME</a><a>ABOUT US</a><a>SERVICES</a><a>SUPPORT</a><a>CLIENTS</a><a>CAREERS</a><a>CONTACT US</a>
</nav>

<section class="hero" role="img" aria-label="Photo of a business team in discussion around a meeting table">
  <div class="hero-tagline display">Let Us Worry About Your Technology… <span class="accent">So You Don't Have To!</span></div>
</section>

<section class="about">
  <div class="about-copy">
    <h2 class="section-title display">ABOUT &nbsp;KELVANBROOK <span class="accent">TECHNOLOGY GROUP, INC</span></h2>
    <div class="rule"></div>
    <p>Kelvanbrook is a technology solution provider based in Ashford, Texas. Our goal is to make technology a non-issue for individuals and small to medium size businesses ranging from 5 to 150 Users. We have the experience, the tools, high-level technology solutions and training to power your business and your work force. We understand that all business's have one goal in common!</p>
    <div class="pillars">
      <div class="pillar">
        <div class="pillar-icon"><svg width="40" height="40" viewBox="0 0 40 40"><circle cx="20" cy="20" r="14" fill="none" stroke="#fff" stroke-width="3"/><circle cx="20" cy="20" r="6" fill="none" stroke="#fff" stroke-width="3"/><path d="M22 22l12 12" stroke="#fff" stroke-width="3"/></svg></div>
        <div><h3>Our Mission</h3><p>Lorem ipsum dolor a sit amet,<br>consectetuer adipisc....{+}</p></div>
      </div>
      <div class="pillar">
        <div class="pillar-icon"><svg width="40" height="40" viewBox="0 0 40 40"><circle cx="20" cy="17" r="9" fill="none" stroke="#fff" stroke-width="3"/><rect x="15" y="27" width="10" height="6" fill="#fff"/><path d="M20 3v-2M6 17H3M37 17h-3M9 7 7 5M31 7l2-2" stroke="#fff" stroke-width="2"/></svg></div>
        <div><h3>Our Vision</h3><p>Lorem ipsum dolor a sit amet,<br>consectetuer adipisc....{+}</p></div>
      </div>
    </div>
  </div>

  <aside class="inquiry">
    <div class="inquiry-tab display">Quick Inquiry</div>
    <form>
      <div class="field">First Name</div>
      <div class="field">Last Name</div>
      <div class="field">Email</div>
      <div class="field">Phone</div>
      <div class="call display"><em>Or</em>Call 1-800-555-0193</div>
      <span class="submit display">Submit</span>
    </form>
  </aside>
</section>

<section class="services">
  <h2 class="section-title display">OUR <span class="accent">SERVICES</span></h2>

  <div class="service-card" style="left:78px">
    <div class="service-icon" style="background:var(--orange)"><svg width="40" height="40" viewBox="0 0 40 40" stroke="#fff" stroke-width="2.5" fill="none"><circle cx="20" cy="20" r="5"/><path d="M20 4v10M20 26v10M4 20h10M26 20h10M9 9l7 7M24 24l7 7M31 9l-7 7M16 24l-7 7"/></svg></div>
    <h4>Managed IT Solutions</h4>
    <p>Duis autem vel eum iriure do in hendrerit in vulputate Duis autem he....</p>
    <span class="more" style="background:var(--orange)">+</span>
  </div>

  <div class="service-card" style="left:442px">
    <div class="service-icon" style="background:#6f6f6f"><svg width="40" height="40" viewBox="0 0 40 40"><circle cx="20" cy="16" r="8" fill="#fff"/><path d="M8 34c2-8 22-8 24 0z" fill="#fff"/><path d="M9 18a11 11 0 0 1 22 0" fill="none" stroke="#fff" stroke-width="2"/></svg></div>
    <h4>Remote Diagnostic &amp; Support</h4>
    <p>Duis autem vel eum iriure do in hendrerit in vulputate Duis autem he....</p>
    <span class="more">+</span>
  </div>

  <div class="service-card" style="left:806px">
    <div class="service-icon" style="background:#6f6f6f"><svg width="40" height="40" viewBox="0 0 40 40" fill="#fff"><rect x="5" y="12" width="13" height="16"/><rect x="22" y="12" width="13" height="16"/><circle cx="20" cy="20" r="4"/></svg></div>
    <h4>Infrastructure Design &amp; Installation</h4>
    <p>Duis autem vel eum iriure do in hendrerit in vulputate Duis autem he....</p>
    <span class="more">+</span>
  </div>
</section>

<section class="testimonials">
  <h2 class="section-title display">CLIENTS <span class="accent">TESTIMONIALS</span></h2>
  <div class="divider"></div>
  <svg class="arrow" style="left:110px" width="30" height="56" viewBox="0 0 30 56"><path d="M28 2 2 28l26 26" fill="none" stroke="#999" stroke-width="1.5"/></svg>
  <svg class="arrow" style="left:1060px" width="30" height="56" viewBox="0 0 30 56"><path d="M2 2l26 26L2 54" fill="none" stroke="#999" stroke-width="1.5"/></svg>
  <p class="quote"><span class="mark">“</span> Lorem ipsum dolor sit amet, consectetuer adipiscing elit, sed diam nonummy nibh euismod tinciduntol ut laoreet dolore magna aliquam erat volutpat. Ut wisi enim ad minim veniam, quis nostrud exercimori mornkle tation ullamcorper suscipit lobortis nisl ut aliquip ex ea commodo consequat. <span class="mark">”</span></p>
  <p class="author">Marla T.</p>
  <p class="place">Bayview, CA</p>
</section>

<footer class="site-footer" role="img" aria-label="Night city skyline photo behind the footer">
  <div class="footer-col" style="left:88px;width:190px">
    <h5>Quick <span class="accent">Links</span></h5>
    <ul class="quick-links"><li>Home</li><li>About Us</li><li>Services</li><li>Support</li><li>Clients</li><li>Careers</li><li>Contact Us</li></ul>
  </div>
  <div class="footer-col contact-lines" style="left:336px;width:260px">
    <h5 style="border:none">Contact <span class="accent">Details</span></h5>
    <p>Kelvanbrook Technology Group, Inc.</p>
    <p>418 Marlow Ave.<br>Ashford, Texas 77990</p>
    <div class="row"><svg width="14" height="14" viewBox="0 0 24 24"><path fill="#f39325" d="M6.6 10.8a15 15 0 0 0 6.6 6.6l2.2-2.2c.3-.3.7-.4 1-.2 1.1.4 2.3.6 3.6.6.6 0 1 .4 1 1V20c0 .6-.4 1-1 1A17 17 0 0 1 3 4c0-.6.4-1 1-1h3.5c.6 0 1 .4 1 1 0 1.2.2 2.4.6 3.6.1.3 0 .7-.2 1z"/></svg>(555) 014-2287</div>
    <div class="row"><svg width="14" height="14" viewBox="0 0 24 24" fill="#f39325"><rect x="6" y="2" width="12" height="6"/><rect x="2" y="9" width="20" height="9" rx="2"/><rect x="6" y="15" width="12" height="7"/></svg>(555) 014-2287</div>
    <div class="row"><svg width="14" height="12" viewBox="0 0 24 18"><rect width="24" height="18" fill="#f39325"/><path d="M0 0l12 10L24 0" fill="none" stroke="#3a3634" stroke-width="2"/></svg>info@kelvanbrook.com</div>
  </div>
  <div class="footer-col social-list" style="left:645px;width:200px">
    <h5 style="border:none">Get <span class="accent">Social</span></h5>
    <div class="row"><span class="sq"></span>Community</div>
    <div class="row"><span class="sq"></span>Updates</div>
    <div class="row"><span class="sq"></span>Circles</div>
    <div class="row"><span class="sq"></span>Network</div>
  </div>
</footer>

<div class="copyright">Copyright © 2017 Kelvanbrook Technology Group, Inc. All Rights Reserved.</div>

</body>
</html>
```